Modern design company business card design

We are a design oriented construction firm. The owner is an architect and licensed General Contractor and accomplished furniture designer. We do new home construction and large scale remodeling and office design. We would like a design for our new business cards that is clean and modern, but relatable. We like the bright green color of our logo mixed with different shades of grey. We're also open to reinterpreting the logo.

Target Market(s)

Potential design clients,
Construction clients

Industry/Entity Type

Architecture

Contact Information for Business Card

Tall Maple Design | Build Inc. (optional with logo, Inc. optional)Jeffrey MorganOwner (optional)317.555.0148 cell317.431.8056 officejmorgan@greensquareinc.comwww.greensquareinc.com

Font styles to use
Sans Serif
Other font styles liked:
• Avenir

Requirements
Nice to have
• I like designs that have some continuity between the front and back, i.e. similar layouts or graphic elements that wrap around the card. I tend to prefer horizontal over vertical, but that's not a have to. I also tend to prefer white or recycled paper.

```html
<!DOCTYPE html>
<html lang="en">
<head>
<meta charset="utf-8">
<title>Tall Maple Design | Build — Business Cards</title>
<link rel="stylesheet" href="https://fonts.googleapis.com/css2?family=Nunito+Sans:wght@400;700&display=swap">
<style>
  :root {
    --backdrop: #b9b9b7;
    --card-black: #111111;
    --card-edge: #1c1c1c;
    --brand-green: #a6d65a;
    --icon-green: #7cc242;
    --text-white: #f2f2f2;
    --text-grey: #8a8a8a;
    --rule-grey: #2e2e2e;
  }
  * { margin: 0; padding: 0; box-sizing: border-box; }
  html, body {
    width: 1200px; height: 900px; overflow: hidden;
    background: var(--backdrop);
    font-family: "Nunito Sans", "Avenir", sans-serif;
  }
  .stage { position: relative; width: 1200px; height: 900px; }

  .card {
    position: absolute;
    width: 600px; height: 343px;
    background: radial-gradient(ellipse at 60% 30%, var(--card-edge), var(--card-black) 70%);
    box-shadow: 0 6px 18px rgba(0,0,0,.25);
  }
  .card--front { left: 480px; top: 80px; }
  .card--back  { left: 120px; top: 470px; }

  /* Wordmark: invented name, one colour, one weight */
  .wordmark {
    position: absolute;
    font-weight: 400;
    text-transform: uppercase;
    line-height: 1.2;
    text-align: right;
  }
  .wordmark__title { display: block; letter-spacing: 3px; }
  .wordmark__sub { display: block; letter-spacing: 3px; }

  .card--front .wordmark { left: 0; right: 0; top: 140px; text-align: center; color: var(--text-white); }
  .card--front .wordmark__title { font-size: 34px; }
  .card--front .wordmark__sub { font-size: 14px; margin-top: 4px; }

  .card--back .wordmark { right: 40px; top: 92px; color: var(--text-grey); }
  .card--back .wordmark__title { font-size: 26px; }
  .card--back .wordmark__sub { font-size: 12px; margin-top: 2px; }

  /* Back card details */
  .person { position: absolute; left: 48px; top: 110px; }
  .person__name { color: var(--brand-green); font-weight: 700; font-size: 19px; }
  .person__role { color: var(--text-white); font-size: 13px; margin-top: 1px; }

  .divider {
    position: absolute; left: 240px; right: 40px; top: 172px;
    height: 1px; background: var(--rule-grey);
  }
  .divider--lower { left: 300px; top: 232px; }

  .contact {
    position: absolute; right: 40px; top: 244px;
    list-style: none;
  }
  .contact__item {
    display: flex; justify-content: flex-end; align-items: center; gap: 10px;
    color: var(--text-white); font-size: 15px; line-height: 21px; letter-spacing: .3px;
  }
  .contact__icon { width: 13px; height: 13px; flex: none; }
</style>
</head>
<body>
<main class="stage">

  <section class="card card--front" aria-label="Card front">
    <p class="wordmark">
      <span class="wordmark__title">Tall Maple</span>
      <span class="wordmark__sub">Design | Build</span>
    </p>
  </section>

  <section class="card card--back" aria-label="Card back">
    <p class="wordmark">
      <span class="wordmark__title">Tall Maple</span>
      <span class="wordmark__sub">Design | Build</span>
    </p>

    <div class="person">
      <p class="person__name">Dennis Holloway</p>
      <p class="person__role">Owner</p>
    </div>

    <div class="divider"></div>
    <div class="divider divider--lower"></div>

    <ul class="contact">
      <li class="contact__item">317.555.0172
        <svg class="contact__icon" viewBox="0 0 16 16" aria-hidden="true"><path fill="#7cc242" d="M3.5 1.5l2.3 2.6-1.3 1.6c.9 2 2.3 3.4 4.3 4.3l1.6-1.3 2.6 2.3-1.3 2c-5.3-.5-9.4-4.6-9.9-9.9z"/></svg>
      </li>
      <li class="contact__item">317.555.0148
        <svg class="contact__icon" viewBox="0 0 16 16" aria-hidden="true"><rect x="4" y="1" width="8" height="14" rx="1.5" fill="none" stroke="#7cc242" stroke-width="1.6"/><rect x="6" y="3.5" width="4" height="7" fill="#7cc242"/></svg>
      </li>
      <li class="contact__item">dholloway@tallmapleinc.example
        <svg class="contact__icon" viewBox="0 0 16 16" aria-hidden="true"><rect x="1" y="3" width="14" height="10" fill="#7cc242"/><path d="M1 3l7 6 7-6" fill="none" stroke="#111" stroke-width="1.3"/></svg>
      </li>
      <li class="contact__item">www.tallmapleinc.example
        <svg class="contact__icon" viewBox="0 0 16 16" aria-hidden="true"><g fill="none" stroke="#7cc242" stroke-width="1.8"><rect x="1.5" y="7" width="7" height="4" rx="2" transform="rotate(-45 5 9)"/><rect x="7.5" y="5" width="7" height="4" rx="2" transform="rotate(-45 11 7)"/></g></svg>
      </li>
    </ul>
  </section>

</main>
</body>
</html>
```